Want a package created for a new protein bar

We would like a new package created for a new protein bar project The name of the bar will be VORNBar a real food protein bar, we would like a ‘window’ on the package of bar like Bold Meadow bar below in images.

VORNBar
‘Super Food Bar’
14g of Whey Protein
The package film size is the following 12cm width x 15cm Length,
Flavor Peanut Chocolate Chip, additional information will be attached shortly like nutrition facts,

Target Market(s)

fitness market, bodybuilders, athletes, everyday people

Industry/Entity Type

Health Product

Logo Text

VORNBar

Font styles to use
Serif
Sans Serif
Decorative

Requirements
Must have
• Package window

```html
<!DOCTYPE html>
<html lang="en">
<head>
<meta charset="UTF-8">
<title>VORNBar – Peanut Chocolate Chip wrapper</title>
<link href="https://fonts.googleapis.com/css2?family=Montserrat:wght@500;600;800&family=Poppins:ital,wght@0,600;0,700;0,800;1,700;1,800&display=swap" rel="stylesheet">
<style>
  :root {
    --stage: #2b2a29;
    --wrapper: #141414;
    --wrapper-edge: #0c0c0c;
    --crimp-line: #262626;
    --white: #f4f4f4;
    --grey: #bdbdbd;
    --red: #d0141b;
    --red-dark: #7e1a1c;
    --oat: #b88a55;
    --oat-dark: #5a3a22;
    --film: rgba(255, 255, 255, 0.55);
  }
  * { margin: 0; padding: 0; box-sizing: border-box; }
  html, body { width: 1200px; height: 1200px; overflow: hidden; }
  body { background: var(--stage); font-family: "Poppins", sans-serif; color: var(--white); position: relative; }

  .wrapper {
    position: absolute; left: 47px; top: 373px; width: 1127px; height: 416px;
    background: linear-gradient(180deg, #1c1c1c 0%, var(--wrapper) 30%, var(--wrapper) 75%, #101010 100%);
  }
  .crimp {
    position: absolute; top: 0; width: 74px; height: 100%;
    background: repeating-linear-gradient(180deg, var(--wrapper-edge) 0 6px, var(--crimp-line) 6px 8px);
  }
  .crimp--left { left: 0; }
  .crimp--right { right: 0; }

  .package-window { position: absolute; left: 0; top: 0; width: 560px; height: 416px; }

  .protein-badge {
    position: absolute; left: 397px; top: 80px; width: 76px; height: 76px; border-radius: 50%;
    background: radial-gradient(circle at 40% 35%, var(--red), var(--red-dark));
  }

  .tagline {
    position: absolute; right: 99px; top: 100px;
    font: italic 800 17px "Poppins", sans-serif; color: var(--white);
  }
  .brand-mark {
    position: absolute; left: 540px; top: 132px; width: 62px; height: 62px; border-radius: 50%;
    background: var(--red-dark);
  }
  .brand-name {
    position: absolute; right: 100px; top: 130px;
    font: 800 70px/1 "Montserrat", sans-serif; color: var(--white); letter-spacing: -1px;
  }
  .claim-band {
    position: absolute; left: 510px; top: 211px; width: 512px; height: 37px;
    background: linear-gradient(90deg, var(--red), var(--red-dark));
    border-radius: 22px 4px 22px 4px;
    font: 500 19px/37px "Montserrat", sans-serif; letter-spacing: 3.4px; padding-left: 20px;
    white-space: nowrap;
  }

  .flavor {
    position: absolute; left: 128px; top: 318px;
    font: italic 800 21px/1.15 "Poppins", sans-serif;
  }
  .sub-brand {
    position: absolute; left: 440px; top: 333px;
    font: 600 17px "Montserrat", sans-serif; letter-spacing: 0.5px;
  }
  .origin { position: absolute; left: 574px; top: 327px; display: flex; align-items: center; gap: 6px; }
  .origin__seal { width: 29px; height: 29px; border-radius: 50%; border: 2px solid var(--white); }
  .origin__text { font: 600 7px/1.2 "Poppins", sans-serif; color: var(--grey); }
  .origin__text b { display: block; font: italic 700 9px "Poppins", sans-serif; color: var(--white); }

  .protein-ring { position: absolute; left: 667px; top: 305px; width: 68px; height: 68px; }
  .protein-ring__label {
    position: absolute; inset: 0; display: flex; flex-direction: column; align-items: center; justify-content: center;
    font: italic 800 17px/1 "Poppins", sans-serif;
  }
  .protein-ring__label small { font: 700 6px "Poppins", sans-serif; margin-top: 2px; }

  .facts {
    position: absolute; left: 760px; top: 322px; width: 256px; height: 45px;
    border: 2px solid var(--white); border-radius: 4px 14px 4px 14px;
    display: grid; grid-template-columns: 1fr 1fr 1fr;
  }
  .facts__cell {
    display: flex; flex-direction: column; align-items: center; justify-content: center;
    font: italic 800 19px/1 "Poppins", sans-serif; text-align: center;
  }
  .facts__cell + .facts__cell { border-left: 2px solid var(--white); }
  .facts__cell small { font: 800 8px/1 "Poppins", sans-serif; margin-top: 1px; }
  .facts__cell--small { font-size: 10px; }
</style>
</head>
<body>
  <div class="wrapper">
    <div class="crimp crimp--left"></div>
    <div class="crimp crimp--right"></div>

    <svg class="package-window" viewBox="0 0 560 416">
      <defs>
        <radialGradient id="bar-tone" cx="40%" cy="45%" r="65%">
          <stop offset="0" stop-color="#b88a55"/>
          <stop offset="0.6" stop-color="#8a5e36"/>
          <stop offset="1" stop-color="#5a3a22"/>
        </radialGradient>
        <radialGradient id="props-tone" cx="50%" cy="50%" r="60%">
          <stop offset="0" stop-color="#c79a62"/>
          <stop offset="1" stop-color="#6b4424"/>
        </radialGradient>
      </defs>
      <path d="M78 160 L388 73 Q400 70 404 82 L452 246 Q455 258 443 261 L104 306 Q92 308 90 296 L70 172 Q68 163 78 160 Z"
            fill="rgba(255,255,255,0.06)" stroke="var(--film)" stroke-width="2"/>
      <polygon points="87,167 388,83 441,248 99,295" fill="url(#bar-tone)"
               role="img" aria-label="Peanut chocolate chip protein bar seen through the clear window"/>
      <ellipse cx="412" cy="272" rx="66" ry="40" fill="url(#props-tone)"
               role="img" aria-label="Peanuts and chocolate chips"/>
    </svg>
    <div class="protein-badge"></div>

    <p class="tagline">Chewy, Crispy, Crunchy</p>
    <div class="brand-mark"></div>
    <h1 class="brand-name">VORNBAR</h1>
    <div class="claim-band">High Protein Snack | Super food bar</div>

    <p class="flavor">Peanut Butter &amp;<br>Chocolate Chip</p>
    <p class="sub-brand">VORNBITES</p>
    <div class="origin">
      <div class="origin__seal"></div>
      <p class="origin__text">Made in<b>Canada</b></p>
    </div>

    <div class="protein-ring">
      <svg width="68" height="68" viewBox="0 0 68 68">
        <circle cx="34" cy="34" r="30" fill="none" stroke="#2e2e2e" stroke-width="5"/>
        <circle cx="34" cy="34" r="30" fill="none" stroke="#d0141b" stroke-width="5"
                stroke-dasharray="43 188" transform="rotate(-90 34 34)"/>
      </svg>
      <div class="protein-ring__label">23%<small>PROTEINS</small></div>
    </div>

    <div class="facts">
      <div class="facts__cell">14g<small>WHEY<br>PROTEIN</small></div>
      <div class="facts__cell">60g</div>
      <div class="facts__cell facts__cell--small">GLUTEN<br>FREE</div>
    </div>
  </div>
</body>
</html>
```